Business Card Design Competition

We need a business card design for our Internet Marketing company. We require both front and back designs and the final card must be 89x53mm in size, plus crop marks to 91x55mm. Colours as per logo, plus perhaps black and/or grey (#828282).
Final text must be editable (if you can supply an editable Fireworks PNG, even better)...
FRONT TEXT:
Full Name
Position
Address Line
Suburb, State, Postcode
Phone: 0000 000 000
Mobile: 0000 000 000
Email: xxx@brightlanemedia.com.au
Web: www.brightlanemedia.com.au
Rear of card should be a fresh design plus our slogan text: "Getting You Noticed" in large font, then in small text "Kestrel Holdings Pty Ltd (ABN: 42 561 903 774)".
Target Market(s)
Small/Medium Businesses
Industry/Entity Type
Business

```html
<!DOCTYPE html>
<html lang="en">
<head>
<meta charset="utf-8">
<title>Brightlane Media – Business Card Front</title>
<link rel="stylesheet" href="https://fonts.googleapis.com/css2?family=Tinos&family=Cormorant+Garamond:wght@500&display=swap">
<style>
  :root {
    --paper-light: #f4f4f4;
    --paper-mid: #e6e6e6;
    --paper-edge: #dcdcdc;
    --ink: #111111;
    --brand-green: #6fae2a;
    --brand-orange: #f28c1e;
  }
  html, body {
    margin: 0;
    padding: 0;
    width: 1200px;
    height: 726px;
    overflow: hidden;
    background: var(--paper-mid);
  }
  .card {
    position: relative;
    width: 1200px;
    height: 726px;
    overflow: hidden;
    background:
      radial-gradient(ellipse at 60% 35%, var(--paper-light) 0%, var(--paper-mid) 70%, var(--paper-edge) 100%);
    font-family: "Tinos", "Times New Roman", serif;
    color: var(--ink);
  }
  .brand {
    position: absolute;
    left: 84px;
    top: 82px;
    display: flex;
    align-items: center;
    gap: 12px;
  }
  .brand-mark {
    display: block;
    width: 82px;
    height: 82px;
  }
  .brand-name {
    font-family: "Tinos", "Times New Roman", serif;
    font-size: 27px;
    line-height: 1;
    color: var(--brand-green);
    white-space: nowrap;
  }
  .contact-line {
    position: absolute;
    left: 0;
    width: 1176px;
    margin: 0;
    text-align: center;
    line-height: 1;
    white-space: nowrap;
    font-weight: 400;
  }
  .person-name   { top: 134px; font-size: 35px; }
  .person-role   { top: 196px; font-size: 31px; font-family: "Cormorant Garamond", "Times New Roman", serif; font-weight: 500; }
  .address       { top: 297px; font-size: 35px; }
  .locality      { top: 400px; font-size: 35px; }
  .phone         { top: 456px; font-size: 35px; }
  .mobile        { top: 503px; font-size: 35px; }
  .email         { top: 551px; font-size: 35px; }
  .web           { top: 597px; font-size: 35px; }
</style>
</head>
<body>
  <main class="card">
    <div class="brand">
      <svg class="brand-mark" viewBox="0 0 82 82" aria-hidden="true">
        <circle cx="41" cy="41" r="40" fill="var(--brand-orange)"/>
      </svg>
      <span class="brand-name">Brightlane Media</span>
    </div>

    <p class="contact-line person-name">Name</p>
    <p class="contact-line person-role">Position</p>
    <p class="contact-line address">Address Line</p>
    <p class="contact-line locality">Suburb, State, Postcode</p>
    <p class="contact-line phone">Phone: 0000 000 000</p>
    <p class="contact-line mobile">Mobile: 0000 000 000</p>
    <p class="contact-line email">Email: xxx@brightlanemedia.com.au</p>
    <p class="contact-line web">Web: www.brightlanemedia.com.au</p>
  </main>
</body>
</html>
```